Investment company needing business card

We are wanting a business card which looks sharp and easy on the eye. We are thinking of having a business card with the logo embossed on it, to really make it stand out. We will only have a small amount of information of the business card, person's name, position, email address and phone number

Contact Information for Business Card

Danielle Frost
Executive Assistant
+64 21 473 5162
danielf@harwickpartners.co.nz

Requirements
Must have
• Embossed logo
Should not have
• Not to be busy

```html
<!DOCTYPE html>
<html lang="en">
<head>
<meta charset="UTF-8">
<title>Harwick Partners – Business Card</title>
<link rel="stylesheet" href="https://fonts.googleapis.com/css2?family=Roboto:wght@400;500&display=swap">
<style>
  :root {
    --bg: #2a2a2b;
    --card: #1f1f20;
    --card-edge: #2c2c2d;
    --emboss: #6e6e70;
    --emboss-light: #8a8a8c;
    --green: #2bbf7a;
    --white: #f2f2f2;
  }
  * { box-sizing: border-box; margin: 0; padding: 0; }
  html, body {
    width: 1200px; height: 900px; overflow: hidden;
    background: var(--bg);
    font-family: "Roboto", Arial, sans-serif;
  }
  .stage {
    width: 1200px; height: 900px;
    display: flex; flex-direction: column; align-items: center; justify-content: center;
    gap: 44px;
  }
  .card {
    width: 640px; height: 366px;
    background: linear-gradient(135deg, var(--card) 0%, var(--card-edge) 100%);
    box-shadow: 0 10px 30px rgba(0,0,0,.45);
    position: relative;
  }
  /* Front */
  .card-front { display: flex; align-items: center; justify-content: center; }
  .wordmark {
    display: flex; align-items: center; gap: 14px;
    font-weight: 500; letter-spacing: 3px; text-transform: uppercase;
  }
  .wordmark-square { width: 34px; height: 34px; }
  .wordmark-front { color: var(--emboss); font-size: 36px; }
  .wordmark-front .wordmark-square { background: var(--emboss); }
  /* Back */
  .card-back { display: flex; align-items: center; padding: 0 40px 0 50px; }
  .card-back .brand { width: 270px; }
  .wordmark-back { color: var(--green); font-size: 22px; gap: 10px; letter-spacing: 2px; }
  .wordmark-back .wordmark-square { width: 24px; height: 24px; background: var(--green); }
  .divider { width: 2px; height: 124px; background: var(--green); margin: 0 34px 0 10px; }
  .details { color: var(--white); }
  .name { color: var(--green); font-size: 30px; font-weight: 500; letter-spacing: 1px; text-transform: uppercase; line-height: 1; }
  .title { font-size: 16px; margin: 4px 0 22px; }
  .contact { list-style: none; font-size: 15px; line-height: 1.55; }
  .contact li { display: flex; align-items: center; gap: 10px; }
  .contact svg { width: 12px; height: 12px; flex: none; }
</style>
</head>
<body>
<main class="stage">
  <section class="card card-front" aria-label="Card front">
    <div class="wordmark wordmark-front">
      <span class="wordmark-square"></span>
      <span>Harwick Partners</span>
    </div>
  </section>

  <section class="card card-back" aria-label="Card back">
    <div class="brand">
      <div class="wordmark wordmark-back">
        <span class="wordmark-square"></span>
        <span>Harwick Partners</span>
      </div>
    </div>
    <div class="divider"></div>
    <div class="details">
      <h1 class="name">Danielle Frost</h1>
      <p class="title">Executive Assistant</p>
      <ul class="contact">
        <li>
          <svg viewBox="0 0 12 12"><path d="M3 1 L5 3.5 L4 5 Q5 7 7 8 L8.5 7 L11 9 L10 11 Q4 11 1 3 Z" fill="var(--green)"/></svg>
          <span>+64 21 473 5162</span>
        </li>
        <li>
          <svg viewBox="0 0 12 12"><rect x="1" y="2.5" width="10" height="7" fill="none" stroke="var(--green)" stroke-width="1.2"/><path d="M1 2.5 L6 7 L11 2.5" fill="none" stroke="var(--green)" stroke-width="1.2"/></svg>
          <span>danielf@harwickpartners.co.nz</span>
        </li>
        <li>
          <svg viewBox="0 0 12 12"><circle cx="6" cy="6" r="5" fill="none" stroke="var(--green)" stroke-width="1.2"/><ellipse cx="6" cy="6" rx="2.2" ry="5" fill="none" stroke="var(--green)" stroke-width="1"/><path d="M1 6 H11" stroke="var(--green)" stroke-width="1"/></svg>
          <span>www.harwickpartners.co.nz</span>
        </li>
      </ul>
    </div>
  </section>
</main>
</body>
</html>
```